Business Card Design for Flood Rescue 360 - Property Restoration Professionals

I need a business card designed for Flood Rescue 360. We are a full-service property restoration solution. Providing water, fire, smoke & storm restoration as well as mold remediation and full remodel or reconstruction to homes and businesses across Dallas-Fort Worth, TX.
Target Market(s)
home and business owners with insurance covered property damage from water, fire or storm related damage
Industry/Entity Type
property restoration
Contact Information for Business Card
Marcus Pelley General Manager Cell: 214-555-0193 Office: 469-555-0148 email: Marcus@FloodRescue360.example services: Water, Fire, Mold, Reconstruction Tagline: Urgency for Your Water Emergency!
Look and feel
Each slider illustrates characteristics of the customer's brand and the style your logo design should communicate.

```html
<!DOCTYPE html>
<html lang="en">
<head>
<meta charset="utf-8">
<title>Flood Rescue 360 – Business Card</title>
<link rel="stylesheet" href="https://fonts.googleapis.com/css2?family=Montserrat:wght@400;500;700;800&display=swap">
<style>
  :root {
    --brand-blue: #16b3e6;
    --ink: #2b2b2b;
    --stripe-gray: #6b6b6b;
    --paper: #ffffff;
    --backdrop: #d2d2d2;
  }
  * { box-sizing: border-box; margin: 0; padding: 0; }
  html, body { width: 1200px; height: 815px; overflow: hidden; }
  body {
    background: var(--backdrop);
    font-family: "Montserrat", Arial, sans-serif;
    position: relative;
  }
  .card {
    position: absolute;
    width: 540px;
    height: 309px;
    border-radius: 24px;
    overflow: hidden;
    box-shadow: 0 10px 24px rgba(0,0,0,0.22);
  }
  .card-front { left: 40px; top: 170px; background: var(--paper); }
  .card-back { left: 620px; top: 336px; background: var(--brand-blue); }

  .front-wave { position: absolute; inset: 0; width: 100%; height: 100%; }

  .side-tab {
    position: absolute; left: 0; top: 76px;
    width: 10px; height: 30px; background: var(--brand-blue);
  }
  .front-brand {
    position: absolute; right: 34px; top: 22px;
    display: flex; align-items: center; gap: 10px;
    color: var(--brand-blue); font-weight: 800;
    font-size: 26px; line-height: 1.02; text-transform: uppercase;
  }
  .brand-dot {
    width: 58px; height: 58px; border-radius: 50%;
    border: 6px solid var(--brand-blue);
    flex: none;
  }
  .person { position: absolute; left: 30px; top: 70px; }
  .person-name {
    color: var(--brand-blue); font-weight: 700; font-size: 22px;
    text-transform: uppercase; letter-spacing: 0.5px;
  }
  .person-title { color: var(--ink); font-size: 12.5px; margin-top: 2px; }
  .contacts { list-style: none; position: absolute; left: 30px; top: 138px; }
  .contacts li {
    display: flex; align-items: center; gap: 8px;
    color: var(--ink); font-size: 11.5px; line-height: 19px;
  }
  .contacts svg { width: 11px; height: 11px; fill: var(--brand-blue); flex: none; }
  .divider {
    position: absolute; left: 30px; top: 221px;
    width: 22px; height: 2px; background: var(--brand-blue);
  }
  .tagline {
    position: absolute; left: 30px; top: 229px;
    color: var(--ink); font-size: 12px;
  }

  .back-brand {
    position: absolute; left: 64px; top: 80px;
    display: flex; align-items: center; gap: 16px;
    color: var(--paper); font-weight: 800; font-size: 44px;
    line-height: 0.98; text-transform: uppercase;
  }
  .back-brand .brand-dot { width: 84px; height: 84px; border: 8px solid var(--paper); }
  .services {
    position: absolute; left: 64px; bottom: 56px;
    display: flex; gap: 14px; list-style: none;
    color: var(--paper); font-size: 15px; font-weight: 500; letter-spacing: 0.6px;
  }
  .services li { display: flex; align-items: center; gap: 8px; }
  .services svg { width: 8px; height: 12px; fill: var(--paper); }
</style>
</head>
<body>

<section class="card card-front" aria-label="Business card front">
  <svg class="front-wave" viewBox="0 0 540 309" preserveAspectRatio="none" aria-hidden="true">
    <path d="M0 282 C200 292 320 236 390 156 C440 100 485 78 540 70 L540 78 C485 86 444 108 395 163 C325 243 205 299 0 289 Z" fill="var(--stripe-gray)"/>
    <path d="M0 298 C200 308 320 252 390 172 C440 116 485 94 540 86 L540 309 L0 309 Z" fill="var(--brand-blue)"/>
  </svg>

  <div class="front-brand">
    <span class="brand-name">Flood<br>Rescue 360</span>
    <span class="brand-dot"></span>
  </div>

  <span class="side-tab"></span>
  <div class="person">
    <p class="person-name">Marcus Pelley</p>
    <p class="person-title">General Manager</p>
  </div>

  <ul class="contacts">
    <li><svg viewBox="0 0 24 24"><path d="M6.6 10.8a15 15 0 0 0 6.6 6.6l2.2-2.2c.3-.3.7-.4 1-.2 1.1.4 2.3.6 3.6.6.6 0 1 .4 1 1V20c0 .6-.4 1-1 1A17 17 0 0 1 3 4c0-.6.4-1 1-1h3.5c.6 0 1 .4 1 1 0 1.3.2 2.5.6 3.6.1.3 0 .7-.2 1z"/></svg>214-555-0193</li>
    <li><svg viewBox="0 0 24 24"><path d="M7 1h10a2 2 0 0 1 2 2v18a2 2 0 0 1-2 2H7a2 2 0 0 1-2-2V3a2 2 0 0 1 2-2zm0 3v14h10V4z"/></svg>469-555-0148</li>
    <li><svg viewBox="0 0 24 24"><path d="M2 5h20v14H2zm2 2v.5l8 5 8-5V7z"/></svg>Marcus@FloodRescue360.example</li>
    <li><svg viewBox="0 0 24 24"><path d="M12 2a10 10 0 1 0 0 20 10 10 0 0 0 0-20zm0 2c.9 0 2.3 2 2.8 5H9.2C9.7 6 11.1 4 12 4zM4.3 11h3.8c0 .7 0 1.3.1 2H4.3a8 8 0 0 1 0-2zm15.4 0a8 8 0 0 1 0 2h-3.9l.1-2zM9.2 15h5.6c-.5 3-1.9 5-2.8 5s-2.3-2-2.8-5z"/></svg>www.FloodRescue360.example</li>
  </ul>
  <span class="divider"></span>
  <p class="tagline">Urgency for Your Water Emergency!</p>
</section>

<section class="card card-back" aria-label="Business card back">
  <div class="back-brand">
    <span class="brand-name">Flood<br>Rescue 360</span>
    <span class="brand-dot"></span>
  </div>
  <ul class="services">
    <li><svg viewBox="0 0 8 12"><path d="M4 0C4 0 0 5 0 8a4 4 0 0 0 8 0C8 5 4 0 4 0z"/></svg>Water</li>
    <li><svg viewBox="0 0 8 12"><path d="M4 0C4 0 0 5 0 8a4 4 0 0 0 8 0C8 5 4 0 4 0z"/></svg>Fire</li>
    <li><svg viewBox="0 0 8 12"><path d="M4 0C4 0 0 5 0 8a4 4 0 0 0 8 0C8 5 4 0 4 0z"/></svg>Mold</li>
    <li><svg viewBox="0 0 8 12"><path d="M4 0C4 0 0 5 0 8a4 4 0 0 0 8 0C8 5 4 0 4 0z"/></svg>Reconstruction</li>
  </ul>
</section>

</body>
</html>
```